BOLD & MINIMALIST DESIGN NEEDED

We want a very bold but minimalistic business card design that is impactful and utilizes both sides of the business card. Our current logo is included for your use.

We want bold fonts and good use of negative space. We don't want the logo to overpower the design.

Target Market(s)

Professionals who are building new commercial buildings.

Industry/Entity Type

Construction

Contact Information for Business Card

Name, Title, email, office phone, cell phone, website

Font styles to use
Serif
Sans Serif

Requirements
Must have
• Bold design!

```html
<!DOCTYPE html>
<html lang="en">
<head>
<meta charset="utf-8">
<title>Ridgeway Design + Build – Business Card</title>
<link href="https://fonts.googleapis.com/css2?family=Poppins:wght@400;500;700;800&display=swap" rel="stylesheet">
<style>
  :root {
    --stage: #e9e7e3;
    --green: #6cbb3c;
    --green-deep: #2f6e16;
    --green-mid: #4f9a26;
    --ink: #111111;
    --text: #3a3a3a;
    --paper: #ffffff;
    --haze: #ececec;
  }
  * { margin: 0; padding: 0; box-sizing: border-box; }
  html, body { width: 1200px; height: 900px; overflow: hidden; }
  body {
    background: var(--stage);
    font-family: "Poppins", sans-serif;
    position: relative;
  }
  .card {
    position: absolute;
    left: 250px;
    width: 700px;
    height: 400px;
    overflow: hidden;
    box-shadow: 0 10px 28px rgba(0,0,0,0.18);
  }
  /* Back side */
  .card-back { top: 40px; }
  .back-pattern {
    position: absolute; inset: 0;
    background:
      radial-gradient(ellipse at 55% 40%, var(--green) 0%, var(--green-mid) 45%, var(--green-deep) 100%);
  }
  .back-brand {
    position: absolute;
    right: 64px; bottom: 120px;
    display: flex; align-items: center; gap: 8px;
    color: var(--paper);
    font-weight: 700;
    font-size: 20px;
    letter-spacing: 1px;
  }
  .back-brand .mark {
    width: 14px; height: 14px; background: var(--paper);
  }
  /* Front side */
  .card-front { top: 470px; background: var(--paper); }
  .front-haze {
    position: absolute;
    left: 120px; top: 150px; width: 420px; height: 250px;
    background: linear-gradient(135deg, rgba(230,230,230,0.0) 0%, var(--haze) 40%, rgba(236,240,232,0.8) 70%, rgba(255,255,255,0) 100%);
  }
  .brand {
    position: absolute;
    top: 58px; right: 70px;
    display: flex; align-items: center; gap: 10px;
  }
  .brand .mark {
    width: 22px; height: 22px; border-radius: 50%; background: var(--green);
  }
  .brand .name {
    font-weight: 800; font-size: 30px; color: var(--ink); letter-spacing: 1px;
  }
  .divider {
    position: absolute; left: 130px; right: 20px; top: 234px;
    height: 1.5px; background: var(--green);
  }
  .person { position: absolute; left: 36px; top: 200px; }
  .person .full-name { font-weight: 700; font-size: 22px; color: var(--ink); line-height: 1.2; }
  .person .role { font-weight: 400; font-size: 18px; color: var(--green); line-height: 1.3; }
  .contacts {
    position: absolute; left: 52px; top: 282px;
    list-style: none; font-size: 17px; color: var(--text);
  }
  .contacts li { display: flex; align-items: center; gap: 12px; height: 26px; }
  .contacts svg { width: 16px; height: 16px; fill: none; stroke: var(--ink); stroke-width: 2; }
  .address {
    position: absolute; right: 40px; top: 258px;
    text-align: right; font-size: 17px; color: var(--text); line-height: 1.4;
  }
  .web-tab {
    position: absolute; right: 0; bottom: 0;
    width: 300px; height: 62px;
    background: var(--green);
    border-top-left-radius: 22px;
    display: flex; align-items: center; justify-content: center;
    font-size: 18px; color: var(--ink); letter-spacing: 1.5px;
  }
  .base-band {
    position: absolute; left: 0; bottom: 0;
    width: 400px; height: 14px; background: var(--ink);
  }
</style>
</head>
<body>

<section class="card card-back">
  <div class="back-pattern" role="img" aria-label="Repeating embossed brand-mark pattern on green"></div>
  <div class="back-brand"><span class="mark"></span>RIDGEWAY</div>
</section>

<section class="card card-front">
  <div class="front-haze" role="img" aria-label="Large faint brand-mark decoration"></div>

  <div class="brand"><span class="mark"></span><span class="name">RIDGEWAY</span></div>

  <div class="divider"></div>

  <div class="person">
    <div class="full-name">Dana Whitfield</div>
    <div class="role">Founder</div>
  </div>

  <ul class="contacts">
    <li>
      <svg viewBox="0 0 16 16"><rect x="4" y="1" width="8" height="14" rx="1.5"/><line x1="7" y1="12.5" x2="9" y2="12.5"/></svg>
      5XX-4XX-8XXX
    </li>
    <li>
      <svg viewBox="0 0 16 16"><path d="M3 2h3l1.5 3.5-2 1.2a8 8 0 0 0 3.8 3.8l1.2-2L14 10v3a1 1 0 0 1-1 1A11 11 0 0 1 2 3a1 1 0 0 1 1-1z"/></svg>
      555-014-2271
    </li>
    <li>
      <svg viewBox="0 0 16 16"><rect x="1.5" y="3.5" width="13" height="9"/><polyline points="1.5,3.5 8,9 14.5,3.5"/></svg>
      info@rdb-build.com
    </li>
  </ul>

  <div class="address">112 Cedar Bend Rd.<br>Millbrook, GA 30000</div>

  <div class="base-band"></div>
  <div class="web-tab">www.rdb-build.com</div>
</section>

</body>
</html>
```